Business Card Design

We are a commercial real estate brokerage in San Francisco, leasing office buildings downtown.
I would like a clean, elegant look. Simple but powerful .

Industry/Entity Type

Business

Contact Information for Business Card

Derek Holloway
lic# 07258143
415.555.0172
derek@velt-commercial.example
velt-commercial.example

```html
<!DOCTYPE html>
<html lang="en">
<head>
<meta charset="utf-8">
<title>VELT Commercial – Business Card</title>
<link href="https://fonts.googleapis.com/css2?family=Jost:wght@500&family=Open+Sans:wght@400;700&display=swap" rel="stylesheet">
<style>
  :root {
    --backdrop: #e6e4e1;
    --card: #f1f1f0;
    --ink: #2f3236;
    --ink-soft: #55585c;
    --brand-blue: #5f7699;
    --panel: #4b4e53;
    --white: #ffffff;
  }
  * { box-sizing: border-box; margin: 0; padding: 0; }
  html, body {
    width: 1200px; height: 768px; overflow: hidden;
    background: var(--backdrop);
  }
  .canvas { position: relative; width: 1200px; height: 768px; }
  .card {
    position: absolute; width: 510px; height: 292px;
    background: var(--card);
    box-shadow: 0 8px 22px rgba(0,0,0,0.18);
    overflow: hidden;
  }
  .card--front { left: 50px; top: 110px; }
  .card--back { left: 640px; top: 360px; }

  .brand {
    display: flex; align-items: center; gap: 16px;
    font-family: "Jost", sans-serif; font-weight: 500;
    color: var(--brand-blue); text-transform: uppercase; line-height: 1;
  }
  .brand-square { background: var(--brand-blue); flex: none; }
  .card--front .brand {
    position: absolute; left: 0; right: 0; top: 50%;
    transform: translateY(-50%); justify-content: center;
  }
  .card--front .brand-square { width: 58px; height: 58px; }
  .card--front .brand-name { font-size: 44px; letter-spacing: 1px; }

  .card--back .brand { position: absolute; left: 30px; top: 34px; gap: 12px; }
  .card--back .brand-square { width: 40px; height: 40px; }
  .card--back .brand-name { font-size: 31px; letter-spacing: 1px; }

  .swoosh { position: absolute; inset: 0; width: 510px; height: 292px; }

  .person {
    position: absolute; left: 30px; top: 102px;
    font-family: "Open Sans", sans-serif; color: var(--ink);
  }
  .person-name { font-size: 17px; font-weight: 700; }
  .person-title { font-size: 10px; color: var(--ink-soft); margin-top: 1px; }

  .contacts {
    position: absolute; left: 30px; top: 160px; list-style: none;
    font-family: "Open Sans", sans-serif; font-size: 12px; color: var(--ink);
  }
  .contacts li { display: flex; align-items: center; gap: 9px; height: 19px; }
  .contacts svg { width: 12px; height: 12px; fill: var(--ink-soft); flex: none; }

  .license {
    position: absolute; right: 26px; bottom: 22px;
    font-family: "Open Sans", sans-serif; font-size: 12px;
    color: var(--white); letter-spacing: 0.5px;
  }
</style>
</head>
<body>
<main class="canvas">

  <section class="card card--front" aria-label="Card front">
    <div class="brand">
      <span class="brand-square"></span>
      <span class="brand-name">VELT Commercial</span>
    </div>
  </section>

  <section class="card card--back" aria-label="Card back">
    <svg class="swoosh" viewBox="0 0 510 292" aria-hidden="true">
      <path d="M215 292 C370 262 455 170 448 0 L462 0 C472 175 390 268 232 292 Z" fill="var(--brand-blue)"/>
      <path d="M262 292 C400 258 478 160 470 0 L510 0 L510 292 Z" fill="var(--panel)"/>
    </svg>

    <div class="brand">
      <span class="brand-square"></span>
      <span class="brand-name">VELT Commercial</span>
    </div>

    <div class="person">
      <p class="person-name">Derek Holloway</p>
      <p class="person-title">Managing Director</p>
    </div>

    <ul class="contacts">
      <li>
        <svg viewBox="0 0 24 24"><path d="M6.6 10.8a15 15 0 0 0 6.6 6.6l2.2-2.2a1 1 0 0 1 1-.25 11.4 11.4 0 0 0 3.6.57 1 1 0 0 1 1 1V20a1 1 0 0 1-1 1A17 17 0 0 1 3 4a1 1 0 0 1 1-1h3.5a1 1 0 0 1 1 1c0 1.25.2 2.45.57 3.57a1 1 0 0 1-.25 1z"/></svg>
        <span>415.555.0172</span>
      </li>
      <li>
        <svg viewBox="0 0 24 24"><path d="M2 5h20v14H2z M4 7v.4l8 5 8-5V7l-8 5z" fill-rule="evenodd"/></svg>
        <span>derek@velt-commercial.example</span>
      </li>
      <li>
        <svg viewBox="0 0 24 24"><circle cx="12" cy="12" r="10"/><path d="M2 12h20M12 2c3 3 3 17 0 20M12 2c-3 3-3 17 0 20" stroke="var(--card)" stroke-width="1.5" fill="none"/></svg>
        <span>www.velt-commercial.example</span>
      </li>
    </ul>

    <p class="license">LIC# 07258143</p>
  </section>

</main>
</body>
</html>
```